Counseling Practice Business Card

I need a professional looking business card incorporating my new logo that was just completed. Card needs to incorporate my name and title, description of my specialty, my address, my phone number, my fax number, my email and my website URL. I need to be able to choose design on/with different paper colors and textures.
I do not have a lot of business card ideas so I am open to anything but I want bold,sharp, clear card without additional designs other than my logo (see attached file info). I am open to different color backgrounds or paper colors including black. I do not like traditional brackets around area codes in phone number or dashes between numbers in phone number. Am open to other ways of presenting including periods between numbers as appropriate. I do not know enough to know what I like yet but I want card to coordinate and work together with my logo. My practice emphasizes natural mental health interventions so any use of color (with background paper color or the blue and green in my logo) that elicits nature is nice. In addition to black, any natural brown or wood looking background might be desirable also. Most of the offerings so far look very similar and boring.

Target Market(s)

Potential therapy clients and other professionals

Contact Information for Business Card

Card information:
Gerald M. Whitcombe, Ph.D.
Licensed Clinical Psychologist
Integrative Health Coach
4812 Marlowe Ridge Blvd SE
Suite 310
Duluth, GA 30096
(770) 415-2983 phone
(770) 581-4096 fax
drgeraldwhitcombe@quillmarsh.net
brightfernwellness.net

Font styles to use
Serif
Sans Serif
Other font styles liked:
• anything that you think looks crisp, clear and easily readable

Requirements
Must have
• Any color used should coordinate with my logo design (see attached files).
• Card should be printed horizontally so top and bottom are longest sides of rectangle.
• Background color or paper color should complement and highlight logo. Do not like a white background. black, grey, brown or any color my logo would blend well with.
Nice to have
• I would like designer to utilize color to highlight letters/name or phone-fax-web symbols.
• Bottom edge of card could be highlighted if appropriate to an idea.
Should not have
• I would NOT want the card to have a pure white background at all.
• No clear cards.
• Cards should be oriented with long sides on bottom and top, NOT sides. DO NOT LIKE THIS THIN TALL ORIENTATION.

```html
<!DOCTYPE html>
<html lang="en">
<head>
<meta charset="utf-8">
<title>Brightfern Wellness – Business Card</title>
<link href="https://fonts.googleapis.com/css2?family=Roboto:wght@400;700&display=swap" rel="stylesheet">
<style>
  :root {
    --bg: #c4e6dc;
    --card-front: #f2f4ec;
    --brand-blue: #1b6fb8;
    --brand-blue-light: #2a8ccc;
    --ink: #3a3a3a;
    --white: #ffffff;
  }
  * { margin: 0; padding: 0; box-sizing: border-box; }
  html, body { width: 1200px; height: 856px; overflow: hidden; }
  body {
    background: var(--bg);
    font-family: "Roboto", Arial, sans-serif;
    position: relative;
  }
  .card {
    position: absolute;
    width: 560px;
    height: 320px;
    border-radius: 28px;
    box-shadow: 0 6px 18px rgba(40, 90, 80, 0.18);
    overflow: hidden;
  }
  /* Back side */
  .card--back {
    left: 580px; top: 80px;
    background: linear-gradient(180deg, var(--brand-blue-light) 0%, var(--brand-blue) 100%);
    color: var(--white);
  }
  .card--back .brand-name {
    position: absolute;
    left: 0; right: 0; top: 110px;
    text-align: center;
    font-size: 46px;
    font-weight: 400;
    color: var(--white);
    letter-spacing: 1px;
  }
  .card--back .brand-url {
    position: absolute;
    left: 0; right: 0; bottom: 48px;
    text-align: center;
    font-size: 15px;
    font-weight: 700;
    color: var(--white);
  }
  /* Front side */
  .card--front {
    left: 70px; top: 450px;
    background: var(--card-front);
  }
  .front-logo {
    position: absolute;
    left: 30px; top: 118px;
    width: 230px;
    font-size: 34px;
    font-weight: 400;
    line-height: 1.1;
    color: var(--brand-blue);
  }
  .divider {
    position: absolute;
    left: 275px; top: 46px;
    width: 2px; height: 228px;
    background: var(--brand-blue);
  }
  .details {
    position: absolute;
    left: 292px; top: 42px;
    right: 14px;
    color: var(--ink);
    font-size: 14px;
    line-height: 1.3;
  }
  .details .person-name {
    font-size: 19px;
    font-weight: 700;
    color: var(--brand-blue);
    margin-bottom: 2px;
    white-space: nowrap;
  }
  .details .address { margin-top: 14px; }
  .contact-list { list-style: none; margin-top: 14px; }
  .contact-list li {
    display: flex; align-items: center; gap: 8px;
    white-space: nowrap;
    font-size: 13.5px;
    line-height: 1.32;
  }
  .contact-list svg { width: 11px; height: 11px; flex: none; }
  .contact-list .link-accent { color: var(--brand-blue); }
</style>
</head>
<body>

  <section class="card card--back" aria-label="Card back">
    <div class="brand-name">Brightfern Wellness</div>
    <div class="brand-url">www.brightfernwellness.net</div>
  </section>

  <section class="card card--front" aria-label="Card front">
    <div class="front-logo">Brightfern Wellness</div>
    <div class="divider"></div>
    <div class="details">
      <div class="person-name">Gerald M. Whitcombe, Ph.D.</div>
      <div class="title">Licensed Clinical Psychologist</div>
      <div class="title">Integrative Health Coach</div>
      <div class="address">4812 Marlowe Ridge Blvd SE<br>Suite 310 Duluth, GA 30096</div>
      <ul class="contact-list">
        <li>
          <svg viewBox="0 0 12 12" aria-hidden="true"><path d="M3 1 L5 3.5 L4 4.8 Q5 7 7.2 8 L8.5 7 L11 9 L9.8 11 Q4.5 10.5 1 2.2 Z" fill="#1b6fb8"/></svg>
          <span>770.415.2983</span>
        </li>
        <li>
          <svg viewBox="0 0 12 12" aria-hidden="true"><rect x="3" y="1" width="6" height="4" fill="#1b6fb8"/><rect x="1" y="5" width="10" height="5" rx="1" fill="#1b6fb8"/></svg>
          <span>770.581.4096</span>
        </li>
        <li>
          <svg viewBox="0 0 12 12" aria-hidden="true"><rect x="1" y="2.5" width="10" height="7" fill="none" stroke="#1b6fb8" stroke-width="1.2"/><path d="M1 3 L6 7 L11 3" fill="none" stroke="#1b6fb8" stroke-width="1.2"/></svg>
          <span>drgeraldwhitcombe@quillmarsh.net</span>
        </li>
        <li>
          <svg viewBox="0 0 12 12" aria-hidden="true"><circle cx="6" cy="6" r="5" fill="none" stroke="#1b6fb8" stroke-width="1.1"/><ellipse cx="6" cy="6" rx="2.2" ry="5" fill="none" stroke="#1b6fb8" stroke-width="1"/><line x1="1" y1="6" x2="11" y2="6" stroke="#1b6fb8" stroke-width="1"/></svg>
          <span>www.<span class="link-accent">brightfernwellness</span>.net</span>
        </li>
      </ul>
    </div>
  </section>

</body>
</html>
```